Business Card Design

Buy and sell properties
Buy and rehab properties
Buy properties for cash
That is what I do but do need a logo
looking for some type of logo or design on it
Just started business
Back of card should say something like BUY HOUSES CASH
Overview: it is a new company. Basically I buy properties wholesale and fix them up and sell them or sell them to other fix and flippers
Background: company is new so not any background
Market: is basically anyone selling a house or buying a house. Someone that needs to sell house fast. Basically I am a cash home buyer!!!

Updates
Email on card should be:   harborlanerealtyinc@mailnest.com

Industry/Entity Type
House
Contact Information for Business Card
Harbor Lane Realty Inc
PO Box 718296
Coral Mill Key FL 33071

Dwight Kallum
dkallum@mailnest.com
305-271-5589

```html
<!DOCTYPE html>
<html lang="en">
<head>
<meta charset="utf-8">
<title>Harbor Lane Realty Inc — Business Card</title>
<link rel="stylesheet" href="https://fonts.googleapis.com/css2?family=Exo+2:wght@300;400;600&display=swap">
<style>
  :root {
    --brand-blue: #2d3192;
    --brand-blue-mid: #3f44a6;
    --brand-blue-soft: #5a5fba;
    --paper: #ffffff;
    --backdrop: #e9e7e2;
    --text-on-blue: #ffffff;
  }
  * { margin: 0; padding: 0; box-sizing: border-box; }
  html, body {
    width: 1200px; height: 858px; overflow: hidden;
    background: var(--backdrop);
    font-family: "Exo 2", sans-serif;
  }
  .stage {
    position: relative; width: 1200px; height: 858px;
    display: flex; justify-content: center; align-items: center; gap: 80px;
  }
  .card {
    position: relative; width: 380px; height: 665px;
    background: var(--paper); overflow: hidden;
    box-shadow: 0 6px 18px rgba(0,0,0,.18);
  }
  .brand-name {
    position: absolute; left: 0; right: 0; text-align: center;
    color: var(--brand-blue); font-weight: 300;
  }
  .brand-name .line-main { display: block; font-size: 50px; line-height: 1; }
  .brand-name .line-sub { display: block; font-size: 33px; line-height: 1.2; }

  /* skyline artwork area */
  .skyline-art {
    position: absolute; left: 0; right: 0; height: 120px;
  }

  /* front */
  .front .brand-name { top: 74px; }
  .front .skyline-art {
    top: 220px;
    background: linear-gradient(to bottom, var(--brand-blue-soft), var(--brand-blue-mid) 60%, var(--brand-blue));
  }
  .front .contact-panel {
    position: absolute; left: 0; right: 0; top: 340px; bottom: 56px;
    background: var(--brand-blue); color: var(--text-on-blue); text-align: center;
  }
  .person-name { font-size: 40px; font-weight: 600; margin-top: 34px; letter-spacing: .5px; }
  .contact-line { font-size: 20px; font-weight: 300; margin-top: 10px; }
  .contact-line.phone { margin-top: 38px; font-size: 22px; }
  .address-strip {
    position: absolute; left: 0; right: 0; bottom: 0; height: 56px;
    display: flex; align-items: center; justify-content: center;
    color: var(--brand-blue); font-size: 19px; font-weight: 400;
  }

  /* back */
  .back { background: var(--brand-blue); }
  .back .brand-name { top: 94px; color: var(--text-on-blue); }
  .back .skyline-art {
    top: 260px;
    background: linear-gradient(to bottom, var(--brand-blue-mid), var(--brand-blue-soft) 55%, #8e91d0);
  }
  .back .lower-panel {
    position: absolute; left: 0; right: 0; top: 380px; bottom: 56px;
    background: var(--paper); display: flex; justify-content: center; align-items: center;
  }
  .tagline { color: var(--brand-blue); font-size: 30px; font-weight: 600; letter-spacing: .5px; }
</style>
</head>
<body>
<main class="stage">
  <section class="card front">
    <h1 class="brand-name"><span class="line-main">Harbor Lane</span><span class="line-sub">Realty Inc</span></h1>
    <div class="skyline-art" role="img" aria-label="Logo artwork: city skyline silhouette with bridges"></div>
    <div class="contact-panel">
      <p class="person-name">Dwight Kallum</p>
      <p class="contact-line phone">305-271-5589</p>
      <p class="contact-line email">harborlanerealtyinc@mailnest.com</p>
    </div>
    <p class="address-strip">PO Box 718296 Coral Mill Key FL 33071</p>
  </section>
  <section class="card back">
    <h2 class="brand-name"><span class="line-main">Harbor Lane</span><span class="line-sub">Realty Inc</span></h2>
    <div class="skyline-art" role="img" aria-label="Logo artwork: city skyline silhouette with bridges"></div>
    <div class="lower-panel"><p class="tagline">BUY HOUSES CASH</p></div>
  </section>
</main>
</body>
</html>
```